The Molar Ledger (Cover Design for Ebook)

I need a cool and exciting eBook cover for my new book, launching very soon!
I want it to stand out and appeal to young professionals with big dreams.
It should be dramatic and bold and avoid cliche or generic photos. Simple design will work as long as it relates to the message of the book. The content will provide ten years of experience from working in the field and achieving success.
Title: The Molar Ledger (at the top)
(Subheading Updated) The secrets to money, motivation and success they don’t teach you in dental school
OR The secrets to success they don't teach you in dental school.
OR The secrets to money, motivation and success
(smaller under title)
Author Updated: Dr R Hollis (place at the bottom)
Updates

Target Market(s)

Ambitious young dentists
See instagram www.pictogrid.example/themolarledger for a sense of the style that I think could work.

Font styles to use
Serif
Sans Serif

Colors

Designer to choose colors to be used in the design.

Requirements
Must have
• Eye catching and cool.
• Show the benefits of success. Money, freedom, luxury
• Clear title and subheading
Nice to have
• Subtle dental reference
• dimensions 1600x2400
Should not have
• Boring photos of dentist/patients, dental clinic, teeth etc,

```html
<!DOCTYPE html>
<html lang="en">
<head>
<meta charset="utf-8">
<title>The Molar Ledger – Ebook Cover</title>
<link rel="stylesheet" href="https://fonts.googleapis.com/css2?family=Bebas+Neue&family=Oswald:wght@300;400&display=swap">
<style>
  :root {
    --paper: #ffffff;
    --title-blue: #0b86d1;
    --ink: #151515;
    --author-orange: #e8742a;
    --hero-lavender: #b9aee0;
    --hero-blue: #9fb0d6;
    --hero-pink: #eab9d6;
    --hero-mist: #e9e6f4;
  }
  html, body {
    margin: 0;
    padding: 0;
    width: 920px;
    height: 1200px;
    overflow: hidden;
    background: var(--paper);
  }
  .cover {
    position: relative;
    width: 920px;
    height: 1200px;
    background: var(--paper);
  }
  .cover__collage {
    position: absolute;
    left: 0;
    top: 0;
    width: 920px;
    height: 660px;
  }
  .collage-tile { stroke: var(--paper); stroke-width: 3; }
  .collage-tile--blue { fill: url(#toneBlue); }
  .collage-tile--lavender { fill: url(#toneLavender); }
  .collage-tile--pink { fill: url(#tonePink); }
  .collage-tile--hero { fill: url(#toneHero); }
  .cover__title {
    position: absolute;
    left: 0;
    right: 0;
    margin: 0;
    text-align: center;
    color: var(--title-blue);
    font-family: "Bebas Neue", "Oswald", sans-serif;
    font-weight: 400;
    line-height: 1;
  }
  .cover__title-main {
    top: 662px;
    font-size: 156px;
    letter-spacing: 0.01em;
  }
  .cover__title-spaced {
    top: 822px;
    font-size: 120px;
    letter-spacing: 0.5em;
    padding-left: 0.5em;
  }
  .cover__subtitle {
    position: absolute;
    left: 0;
    right: 0;
    top: 950px;
    margin: 0;
    text-align: center;
    color: var(--ink);
    font-family: "Oswald", sans-serif;
    font-weight: 300;
    font-size: 36px;
    line-height: 1.2;
  }
  .cover__author {
    position: absolute;
    left: 0;
    right: 0;
    top: 1080px;
    margin: 0;
    text-align: center;
    color: var(--author-orange);
    font-family: "Oswald", sans-serif;
    font-weight: 400;
    font-size: 58px;
    line-height: 1;
    letter-spacing: 0.35em;
    padding-left: 0.35em;
  }
</style>
</head>
<body>
  <main class="cover">
    <svg class="cover__collage" viewBox="0 0 920 660" role="img" aria-label="Collage of photographed bright smiles in soft blue, lavender and pink tones">
      <defs>
        <linearGradient id="toneBlue" x1="0" y1="0" x2="1" y2="1">
          <stop offset="0" stop-color="var(--hero-mist)"/>
          <stop offset="1" stop-color="var(--hero-blue)"/>
        </linearGradient>
        <linearGradient id="toneLavender" x1="0" y1="0" x2="1" y2="1">
          <stop offset="0" stop-color="var(--hero-mist)"/>
          <stop offset="1" stop-color="var(--hero-lavender)"/>
        </linearGradient>
        <linearGradient id="tonePink" x1="0" y1="0" x2="1" y2="1">
          <stop offset="0" stop-color="var(--hero-mist)"/>
          <stop offset="1" stop-color="var(--hero-pink)"/>
        </linearGradient>
        <linearGradient id="toneHero" x1="0" y1="0" x2="1" y2="1">
          <stop offset="0" stop-color="var(--hero-blue)"/>
          <stop offset="0.55" stop-color="var(--hero-lavender)"/>
          <stop offset="1" stop-color="var(--hero-pink)"/>
        </linearGradient>
      </defs>
      <g class="collage">
        <rect class="collage-tile collage-tile--blue" x="75" y="40" width="145" height="135"/>
        <rect class="collage-tile collage-tile--lavender" x="290" y="35" width="160" height="115"/>
        <rect class="collage-tile collage-tile--pink" x="455" y="55" width="150" height="165"/>
        <rect class="collage-tile collage-tile--pink" x="600" y="70" width="225" height="175"/>
        <rect class="collage-tile collage-tile--blue" x="12" y="150" width="150" height="150"/>
        <rect class="collage-tile collage-tile--lavender" x="625" y="220" width="140" height="160"/>
        <rect class="collage-tile collage-tile--pink" x="500" y="230" width="125" height="175"/>
        <rect class="collage-tile collage-tile--blue" x="88" y="290" width="95" height="80"/>
        <rect class="collage-tile collage-tile--blue" x="130" y="385" width="125" height="140"/>
        <rect class="collage-tile collage-tile--lavender" x="495" y="405" width="215" height="185"/>
        <rect class="collage-tile collage-tile--blue" x="265" y="500" width="110" height="140"/>
        <rect class="collage-tile collage-tile--lavender" x="365" y="510" width="135" height="80"/>
        <rect class="collage-tile collage-tile--hero" x="167" y="150" width="345" height="330"/>
      </g>
    </svg>

    <h1 class="cover__title cover__title-main">THE MOLAR</h1>
    <p class="cover__title cover__title-spaced">LEDGER</p>
    <p class="cover__subtitle">The Secrets to Money, Motivation and Success</p>
    <p class="cover__author">Rowan Hollis</p>
  </main>
</body>
</html>
```